New Dental Office Needs an Attractive and user friendly Website Designed

I need a website for a new dental office. The Name is Harrowfield Dentistry. I would like a Modern design with a user friendly interface and usability.
I would like a landing page, a page that lists the services we offer: Cosmetic Dentistry, Implants, Dental Hygiene, Emergency Services, Restorations, Dentures
Target Market(s)
Mid to upper class
Industry/Entity Type
Dentistry
Coding
Number of Pages Required
1 page
Requirements
Must have
- Landing page that has a scheduling option, Procedures, operating hours, and contact us info
Nice to have
- Appealing design, Soft comforting colors. Easy to navigate page, Modern and professional.

```html
<!DOCTYPE html>
<html lang="en">
<head>
<meta charset="utf-8">
<title>Harrowfield Dentistry</title>
<link href="https://fonts.googleapis.com/css2?family=Marcellus&family=Outfit:ital,wght@0,300;0,400;0,500;0,600;1,300&display=swap" rel="stylesheet">
<style>
:root{
  --ink:#1b1d1c;
  --muted:#6d716f;
  --green:#b2f59c;
  --green-2:#c8f59a;
  --mint:#c5efe3;
  --sky:#cfe3f8;
  --soft:#f4f4f4;
  --line:#e3e5e4;
  --white:#ffffff;
}
*{box-sizing:border-box;margin:0;padding:0}
html,body{width:1200px;height:4323px;overflow:hidden;background:var(--white)}
body{position:relative;font-family:"Outfit",sans-serif;color:var(--ink)}
.abs{position:absolute}
.brand{font-family:"Outfit",sans-serif;font-weight:600;color:var(--ink);letter-spacing:.5px;line-height:1.05}
.btn{position:absolute;display:flex;align-items:center;justify-content:center;gap:8px;border-radius:40px;font-size:14px;font-weight:500;color:var(--ink);background:linear-gradient(90deg,var(--green),var(--green-2))}
.btn.blue{background:var(--sky)}
.btn svg{width:18px;height:12px}
.nav a{position:absolute;top:36px;font-size:14px;color:var(--ink);text-decoration:none}
.nav a.active{border-bottom:1px solid var(--ink);padding-bottom:8px}
.photo{position:absolute}
h2.section{position:absolute;font-weight:500;font-size:37px;letter-spacing:-.3px;line-height:1.1}
.feature{position:absolute;border-radius:16px;background:var(--soft);padding:0 55px}
.feature h3{font-size:20px;font-weight:500;margin-top:14px}
.feature p{font-size:15px;color:var(--muted);margin-top:4px}
.feature svg{width:62px;height:62px;stroke:var(--ink);fill:none;stroke-width:1.6}
.svc{position:absolute;background:var(--soft);border-radius:55px;padding:20px 46px}
.svc h4{font-size:17px;font-weight:500}
.svc p{font-size:12.5px;color:var(--muted);line-height:1.5;margin-top:5px}
.svc.right{text-align:right}
.dot{position:absolute;width:78px;height:78px;border-radius:50%;background:var(--green);display:flex;align-items:center;justify-content:center}
.dot svg{width:40px;height:40px;stroke:#4c7d45;fill:none;stroke-width:1.6}
.field{position:absolute;height:48px;border-radius:26px;background:var(--soft);font-size:13px;font-weight:500;padding:16px 26px}
.footer h5{position:absolute;top:4006px;font-size:22px;font-weight:500}
.footer .link{position:absolute;left:472px;font-size:13px}
.hours{position:absolute;left:711px;font-size:13px;line-height:1.5}
.hours::before{content:"";position:absolute;left:-22px;top:4px;width:11px;height:11px;border-radius:50%;background:var(--sky)}
.social{position:absolute;top:4054px;border-radius:50%}
</style>
</head>
<body>

<!-- Header -->
<div class="brand abs" style="left:89px;top:28px;font-size:24px">Harrowfield<br><span style="font-size:24px">Dentistry</span></div>
<nav class="nav">
  <a class="active" href="#" style="left:520px">Home</a>
  <a href="#" style="left:591px">About Us</a>
  <a href="#" style="left:680px">Services</a>
  <a href="#" style="left:763px">New Patients</a>
  <a href="#" style="left:878px">Contact</a>
</nav>
<a class="btn" style="left:955px;top:22px;width:159px;height:45px;font-weight:600;font-size:13px">Book Appointment</a>

<!-- Hero -->
<div class="photo" role="img" aria-label="Smiling young woman giving two thumbs up" style="left:89px;top:88px;width:1026px;height:554px;border-radius:28px;background:linear-gradient(90deg,var(--mint),#d8ebe6 55%,var(--sky))"></div>
<div class="abs" style="left:104px;top:103px;width:469px;height:524px;border-radius:22px;background:var(--white)"></div>
<h1 class="abs" style="left:104px;top:308px;width:469px;text-align:center;font-family:'Marcellus',serif;font-weight:400;font-size:50px;line-height:1">Smile Brighter</h1>
<p class="abs" style="left:104px;top:370px;width:469px;text-align:center;font-size:19px">With Harrowfield Dentistry</p>
<a class="btn" style="left:158px;top:416px;width:206px;height:46px">Schedule Your Visit <svg viewBox="0 0 18 12"><path d="M1 6h15M11 1l5 5-5 5" stroke="#1b1d1c" fill="none" stroke-width="1.5"/></svg></a>
<a class="btn blue" style="left:374px;top:416px;width:133px;height:46px">Call Now <svg viewBox="0 0 18 12"><path d="M1 6h15M11 1l5 5-5 5" stroke="#1b1d1c" fill="none" stroke-width="1.5"/></svg></a>

<!-- Features -->
<h2 class="section" style="left:0;width:1200px;text-align:center;top:720px">Exceptional Care, Beautiful Results</h2>
<div class="photo" role="img" aria-label="Smiling woman in blue scrubs with hands at her cheeks" style="left:89px;top:831px;width:290px;height:418px;border-radius:16px;background:linear-gradient(160deg,var(--mint),var(--sky))"></div>
<div class="feature" style="left:398px;top:831px;width:439px;height:202px;padding-top:34px">
  <svg viewBox="0 0 62 62"><circle cx="20" cy="20" r="11"/><circle cx="20" cy="20" r="4"/><path d="M28 22c4-6 14-6 18 0 3 5 0 11-1 16-1 6-3 12-6 12-3 0-3-8-6-8s-3 8-6 8-5-7-5-13c0-5 2-10 6-15z"/></svg>
  <h3>Experienced Dentists</h3><p>Over 15 years of trusted care.</p>
</div>
<div class="feature" style="left:847px;top:831px;width:260px;height:202px;background:linear-gradient(135deg,var(--green),var(--green-2));text-align:center;padding:34px 20px 0">
  <svg viewBox="0 0 62 62"><circle cx="31" cy="31" r="22"/><circle cx="31" cy="31" r="14"/><path d="M31 3v6M31 53v6M3 31h6M53 31h6M11 11l4 4M47 47l4 4M51 11l-4 4M11 51l4-4"/></svg>
  <h3 style="margin-top:6px">Advanced Technology</h3><p style="color:#3f4a3d">Precision tools for<br>modern</p>
</div>
<div class="feature" style="left:398px;top:1046px;width:257px;height:203px;background:linear-gradient(135deg,var(--mint),var(--sky));text-align:center;padding:36px 10px 0">
  <svg viewBox="0 0 62 62"><path d="M31 20c3-7 15-7 15 2 0 8-15 16-15 16S16 30 16 22c0-9 12-9 15-2z"/><path d="M6 40c5-2 10 0 14 4l6 6M56 40c-5-2-10 0-14 4l-6 6M8 30v14l10 10M54 30v14L44 54"/></svg>
  <h3 style="margin-top:4px">Patient-Centered</h3><p style="color:var(--ink)">We treat you like a family.</p>
</div>
<div class="feature" style="left:669px;top:1046px;width:441px;height:203px;padding:40px 46px 0">
  <svg viewBox="0 0 62 62"><rect x="4" y="10" width="54" height="46" rx="6"/><path d="M16 4v12M31 4v12M46 4v12M4 22h54"/><circle cx="17" cy="32" r="4"/><circle cx="31" cy="32" r="4"/><circle cx="45" cy="32" r="4"/><circle cx="17" cy="45" r="4"/><circle cx="31" cy="45" r="4"/><circle cx="45" cy="45" r="4"/></svg>
  <h3>Flexible Scheduling</h3><p>Evening &amp; weekend hours available.</p>
</div>

<!-- Services -->
<h2 class="section" style="left:89px;top:1336px;font-weight:600;line-height:1.08">Comprehensive<br>Dental Services<br>Under One Roof</h2>
<p class="abs" style="left:495px;top:1372px;width:350px;font-size:13px;color:var(--muted);line-height:1.5">Feel free to get in touch with Harrowfield dentistry Clinic for general dentistry, specialist treatments or facial aesthetics.</p>
<a class="btn" style="left:930px;top:1375px;width:187px;height:47px;font-size:13px">View All Services <svg viewBox="0 0 18 12"><path d="M1 6h15M11 1l5 5-5 5" stroke="#1b1d1c" fill="none" stroke-width="1.5"/></svg></a>

<svg class="abs" style="left:0;top:1400px" width="1200" height="900" viewBox="0 1400 1200 900">
  <circle cx="576" cy="1882" r="354" fill="none" stroke="var(--line)" stroke-width="1.5"/>
  <circle cx="576" cy="1882" r="297" fill="none" stroke="var(--line)" stroke-width="1.5"/>
</svg>
<div class="photo" role="img" aria-label="Close-up smile split between stained and whitened teeth" style="left:419px;top:1725px;width:314px;height:314px;border-radius:50%;background:linear-gradient(90deg,#d99a86 0 49.5%,#fff 49.5% 50.5%,#e9a0a0 50.5%)"></div>

<div class="svc" style="left:745px;top:1513px;width:369px;height:110px"><h4>Cosmetic Dentistry</h4><p>Feel free to get in touch with Harrowfield den-<br>tistry Clinic for general dentistry, specialist...</p></div>
<div class="svc right" style="left:94px;top:1628px;width:368px;height:108px"><h4>Dental Implants</h4><p>Feel free to get in touch with Harrowfield dentistry<br>Clinic for general dentistry, specialist...</p></div>
<div class="svc" style="left:745px;top:2010px;width:369px;height:108px"><h4>Dental Hygiene &amp; Cleanings</h4><p>Feel free to get in touch with Harrowfield den-<br>tistry Clinic for general dentistry, specialist...</p></div>
<div class="svc right" style="left:93px;top:2081px;width:367px;height:108px"><h4>Emergency Dentistry</h4><p>Feel free to get in touch with Harrowfield dentistry<br>Clinic for general dentistry, specialist...</p></div>

<div class="dot" style="left:438px;top:1562px"><svg viewBox="0 0 40 40"><circle cx="20" cy="20" r="17"/><path d="M13 16c2-4 12-4 14 0 1 4-1 7-1 10s-2 6-3 6-1-5-3-5-2 5-3 5-3-3-3-6-2-6-1-10z"/></svg></div>
<div class="dot" style="left:694px;top:1607px"><svg viewBox="0 0 40 40"><path d="M12 14c3-5 13-5 16 0 2 4-1 9-1 13s-2 7-3 7-1-6-4-6-3 6-4 6-3-3-3-7-3-9-1-13z"/><path d="M8 6l3 3M32 6l-3 3M20 3v4"/></svg></div>
<div class="dot" style="left:820px;top:1919px"><svg viewBox="0 0 40 40"><path d="M11 12c3-6 15-6 18 0 2 5-1 10-1 15s-2 9-4 9-1-8-4-8-2 8-4 8-4-4-4-9-3-10-1-15z"/></svg></div>
<div class="dot" style="left:291px;top:1985px"><svg viewBox="0 0 40 40"><circle cx="20" cy="20" r="17"/><path d="M13 16c2-4 12-4 14 0 1 4-1 7-1 10s-2 6-3 6-1-5-3-5-2 5-3 5-3-3-3-6-2-6-1-10z"/></svg></div>

<!-- Meet your dentist -->
<div class="abs" style="left:89px;top:2317px;width:1026px;height:495px;border-radius:26px;background:var(--soft)"></div>
<div class="photo" role="img" aria-label="Smiling female dentist in white coat with glasses and stethoscope beside a dental chair" style="left:89px;top:2317px;width:560px;height:495px;border-radius:26px 0 0 26px;background:linear-gradient(90deg,#e4e6e7,#eef0f0 70%,var(--soft))"></div>
<h2 class="section" style="left:669px;top:2500px;font-weight:500">Meet Your Dentist</h2>
<p class="abs" style="left:669px;top:2553px;width:360px;font-size:13px;color:var(--muted);line-height:1.5">My goal is to make every patient feel at home while receiving the highest quality care.</p>
<a class="btn" style="left:669px;top:2613px;width:270px;height:50px;font-size:13.5px">Learn More About Our Team <svg viewBox="0 0 18 12"><path d="M1 6h15M11 1l5 5-5 5" stroke="#1b1d1c" fill="none" stroke-width="1.5"/></svg></a>

<!-- Testimonials -->
<h2 class="section" style="left:0;width:1200px;text-align:center;top:2944px;font-weight:500">What Our Patients Are Saying</h2>
<p class="abs" style="left:200px;top:2995px;width:800px;text-align:center;font-size:17px;font-style:italic;font-weight:300;color:var(--muted);line-height:1.6">Harrowfield Dentistry combines the latest technology with the kind of personalized care that’s hard to find these days. They took the time to explain every procedure and made me feel completely at ease.</p>
<p class="abs" style="left:0;width:1200px;text-align:center;top:3086px;font-size:13px;font-weight:500">Marcus T</p>
<div class="abs" style="left:580px;top:3126px;width:11px;height:11px;border-radius:50%;background:#cfd2d1"></div>
<div class="abs" style="left:595px;top:3126px;width:11px;height:11px;border-radius:50%;background:#7cd06d"></div>
<div class="abs" style="left:610px;top:3126px;width:11px;height:11px;border-radius:50%;background:#cfd2d1"></div>

<!-- Contact -->
<div class="abs" style="left:89px;top:3228px;width:1028px;height:524px;border-radius:26px;background:linear-gradient(90deg,var(--mint),var(--sky))"></div>
<h2 class="section" style="left:160px;top:3424px;font-weight:500;line-height:1.15">Have a Question?<br>We’re Happy to Help.</h2>
<p class="abs" style="left:160px;top:3514px;width:340px;font-size:13px;color:var(--muted);line-height:1.5">Feel free to get in touch with Harrowfield dentistry Clinic for general dentistry, specialist treatments or facial aesthetics.</p>
<form class="abs" style="left:622px;top:3265px;width:468px;height:454px;border-radius:22px;background:var(--white)"></form>
<div class="field" style="left:642px;top:3301px;width:207px">First Name*</div>
<div class="field" style="left:859px;top:3301px;width:208px">Last Name*</div>
<div class="field" style="left:642px;top:3367px;width:207px">Email*</div>
<div class="field" style="left:859px;top:3367px;width:208px">Phone*</div>
<div class="field" style="left:642px;top:3432px;width:207px">Address*</div>
<div class="field" style="left:859px;top:3432px;width:208px">Company*</div>
<div class="field" style="left:642px;top:3500px;width:425px;height:126px">Send Your Message*</div>
<a class="btn" style="left:775px;top:3645px;width:157px;height:47px;font-size:13px">Submit Now <svg viewBox="0 0 18 12"><path d="M1 6h15M11 1l5 5-5 5" stroke="#1b1d1c" fill="none" stroke-width="1.5"/></svg></a>

<!-- CTA -->
<h2 class="section" style="left:167px;top:3812px;font-size:36px;font-weight:500">Ready to Prioritize Your Smile?</h2>
<p class="abs" style="left:169px;top:3864px;font-size:13px;color:var(--muted)">Booking your visit is quick and easy. New patients welcome!</p>
<a class="btn" style="left:762px;top:3828px;width:161px;height:44px;font-size:13px">Book Appointment</a>
<a class="btn blue" style="left:937px;top:3828px;width:114px;height:44px;font-size:12px;font-weight:600">555 204 - 318</a>
<div class="abs" style="left:89px;top:3919px;width:1026px;height:1px;background:var(--line)"></div>

<!-- Footer -->
<footer class="footer">
  <div class="brand abs" style="left:89px;top:4070px;font-size:40px">Harrowfield<br>Dentistry</div>
  <h5 style="left:472px">Quick Links</h5>
  <a class="link" style="top:4055px">Home</a>
  <a class="link" style="top:4087px">About Us</a>
  <a class="link" style="top:4119px">Services</a>
  <a class="link" style="top:4151px">New Patients</a>
  <a class="link" style="top:4183px">Contact</a>
  <h5 style="left:687px">Operating Hours</h5>
  <div class="hours" style="top:4052px">Mon – Fri :<br>8:00 AM – 6:00 PM</div>
  <div class="hours" style="top:4107px">Saturday :<br>9:00 AM – 2:00 PM</div>
  <div class="abs" style="left:711px;top:4165px;font-size:13px;line-height:1.5">Sunday :<br><span style="border-bottom:1px solid var(--ink)">Closed</span></div>
  <h5 style="left:969px">Follow Us</h5>
  <div class="social" role="img" aria-label="Social profile" style="left:965px;width:44px;height:44px;background:#2e4aa8"></div>
  <div class="social" role="img" aria-label="Video channel" style="left:1030px;top:4066px;width:20px;height:20px;background:var(--ink)"></div>
  <div class="social" role="img" aria-label="Photo profile" style="left:1084px;top:4066px;width:20px;height:20px;border:1.6px solid var(--ink)"></div>
  <div class="abs" style="left:89px;top:4280px;width:1026px;height:1px;background:var(--line)"></div>
  <p class="abs" style="left:0;width:1200px;text-align:center;top:4299px;font-size:13px">© 2025 Harrowfield Dentistry. All Rights Reserved.</p>
  <div class="abs" style="left:1117px;top:4257px;width:40px;height:40px;border-radius:50%;background:var(--green);display:flex;align-items:center;justify-content:center"><svg width="14" height="16" viewBox="0 0 14 16"><path d="M7 15V2M2 7l5-5 5 5" stroke="#1b1d1c" fill="none" stroke-width="1.5"/></svg></div>
</footer>

</body>
</html>
```